Small Business Broker Business Card Design

A business card design for a small business brokerage, which is a financial service, not unlike real estate brokerage, but for small businesses such as laundromats, pizza shops, restaurants, cleaners etc. The designs should all be simple, more conservative in nature, using the colors and font of the logo. Again, think real estate Brokerage as a business context
Contact Information for Business Card
Name: Glen R. Harlow. Title: Small Business Advisor. Email: g.harlow@bayfieldcapitalworks.example. Mobile: (555) 274-3918. Office: (555) 806-2147. www.bayfieldcapitalworks.example

```html
<!DOCTYPE html>
<html lang="en">
<head>
<meta charset="utf-8">
<title>Bayfield Capital Works – Business Card</title>
<link href="https://fonts.googleapis.com/css2?family=Montserrat:wght@600;700;800&family=Arimo:wght@400&display=swap" rel="stylesheet">
<style>
  :root{
    --navy:#1b3566;
    --green:#7cbf36;
    --green-dark:#5e9c22;
    --green-light:#8fd043;
    --ink:#6b6b6b;
    --paper:#ffffff;
    --backdrop:#1a1a1a;
  }
  *{margin:0;padding:0;box-sizing:border-box}
  html,body{width:1200px;height:963px;overflow:hidden;background:var(--backdrop)}
  .stage{width:1200px;height:963px;display:flex;flex-direction:column;align-items:center;justify-content:center;gap:56px}
  .card{width:660px;height:377px;border-radius:26px;position:relative;overflow:hidden}

  /* front */
  .card-front{background:var(--paper);display:flex;align-items:center;padding:0 30px}
  .brand{width:300px;flex:none;display:flex;flex-direction:column;align-items:flex-start}
  .brand-name{font-family:"Montserrat",sans-serif;font-weight:800;font-size:16px;line-height:1.15;color:var(--navy);text-transform:uppercase;letter-spacing:.4px;white-space:nowrap;display:flex;align-items:center;gap:8px}
  .brand-square{width:12px;height:12px;background:var(--navy);flex:none}
  .brand-tagline{margin-top:7px;font-family:"Montserrat",sans-serif;font-weight:600;font-size:7.6px;letter-spacing:.8px;text-transform:uppercase;white-space:nowrap;color:var(--green)}
  .divider{width:1.5px;height:180px;background:var(--green);margin:0 22px 0 6px;flex:none}
  .person{display:flex;flex-direction:column;min-width:0}
  .person-name{font-family:"Montserrat",sans-serif;font-weight:800;font-size:23px;color:var(--navy);text-transform:uppercase;letter-spacing:.5px;white-space:nowrap}
  .person-title{font-family:"Arimo",sans-serif;font-size:15px;color:var(--green);margin-bottom:14px}
  .contact-list{list-style:none;font-family:"Arimo",sans-serif;font-size:12.5px;color:var(--ink);display:flex;flex-direction:column;gap:6px}
  .contact-list li{display:flex;align-items:center;gap:7px;white-space:nowrap}
  .contact-icon{width:12px;height:12px;flex:none;stroke:var(--green);fill:none;stroke-width:1.6;stroke-linecap:round;stroke-linejoin:round}

  /* back */
  .card-back{background:linear-gradient(135deg,var(--green-light),var(--green) 55%,var(--green-dark))}
  .back-pattern{position:absolute;inset:0}
  .back-brand{position:absolute;right:38px;bottom:34px;font-family:"Montserrat",sans-serif;font-weight:800;font-size:15px;color:var(--paper);text-transform:uppercase;letter-spacing:.5px}
</style>
</head>
<body>
<main class="stage">
  <section class="card card-front">
    <div class="brand">
      <div class="brand-name"><span class="brand-square"></span><span>Bayfield Capital Works, Inc</span></div>
      <div class="brand-tagline">Trusted guidance to buy or sell a business</div>
    </div>
    <div class="divider"></div>
    <div class="person">
      <h1 class="person-name">Glen R. Harlow</h1>
      <p class="person-title">Small Business Advisor</p>
      <ul class="contact-list">
        <li><svg class="contact-icon" viewBox="0 0 16 16"><path d="M4 2l2.5 3-1.5 1.5a8 8 0 0 0 4.5 4.5L11 9.5l3 2.5-1.5 2.5C7 14 2 9 1.5 3.5z"/></svg>(555) 806-2147</li>
        <li><svg class="contact-icon" viewBox="0 0 16 16"><rect x="4" y="1.5" width="8" height="13" rx="1.5"/><path d="M7 12.2h2"/></svg>(555) 274-3918</li>
        <li><svg class="contact-icon" viewBox="0 0 16 16"><rect x="1.5" y="3.5" width="13" height="9" rx="1"/><path d="M1.5 4l6.5 5 6.5-5"/></svg>g.harlow@bayfieldcapitalworks.example</li>
        <li><svg class="contact-icon" viewBox="0 0 16 16"><circle cx="8" cy="8" r="6.5"/><path d="M1.5 8h13M8 1.5c-3 3.5-3 9.5 0 13M8 1.5c3 3.5 3 9.5 0 13"/></svg>www.bayfieldcapitalworks.example</li>
      </ul>
    </div>
  </section>

  <section class="card card-back">
    <div class="back-pattern" role="img" aria-label="Embossed repeating brand pattern in tonal greens"></div>
    <div class="back-brand">Bayfield Capital Works</div>
  </section>
</main>
</body>
</html>
```